Bright Harbor Counseling Letterhead for hip modern business

I would like some ombre use of the colors in the logo hip letterhead that incorporates logo colors and feel, needs to connect with young professionals and college students. i need to be able to write letters to schools to excuse absences as well. i like color blocks on one side preferably using colors from the attached logo design.

Target Market(s)

high income young people, young adults and college students

Industry/Entity Type

mental health

Font styles to use
Serif
Sans Serif

Colors
0054AA
0677BA
7BADD7
CADEEF
E8F1F8
0094D4
00A9DD
6FCCEA
C7EBF8
E9F6FB
00AB8E
00BBA5
67D7C9
C6EFE9
E9F9F6
59FF00
82FF00
B8FF75
E3FFCB
F4FFEA
A7469A
B969AE
D3A5CF
EDDBEB
F8F0F9
6B429C
8869AF
B7A5CE
E3DAEB
F3F0F8

Requirements
Must have
• a modern hip feel, somewhat color

```html
<!DOCTYPE html>
<html lang="en">
<head>
<meta charset="utf-8">
<title>Bright Harbor Counseling – Letterhead and Envelope</title>
<link rel="stylesheet" href="https://fonts.googleapis.com/css2?family=Open+Sans:wght@300;400;600&display=swap">
<style>
  :root {
    --backdrop: #ebebed;
    --paper: #ffffff;
    --ink: #3d3d40;
    --ink-soft: #6a6a70;
    --brand-name: #4a4a50;
    --blue: #0677BA;
    --purple: #A7469A;
    --violet: #6B429C;
    --teal: #00AB8E;
    --mist-purple: #EDDBEB;
    --mist-blue: #E9F6FB;
    --flap-line: #e2e2e6;
  }
  * { box-sizing: border-box; margin: 0; padding: 0; }
  html, body { width: 1200px; height: 795px; overflow: hidden; }
  body {
    background: var(--backdrop);
    font-family: "Open Sans", Arial, sans-serif;
    color: var(--ink);
    position: relative;
  }

  /* Letterhead sheet */
  .letterhead {
    position: absolute;
    left: 70px; top: 45px;
    width: 498px; height: 705px;
    background: var(--paper);
    box-shadow: 0 6px 22px rgba(0,0,0,0.10);
    padding: 48px 46px 40px 50px;
    overflow: hidden;
  }
  .brand {
    display: flex;
    justify-content: flex-end;
    align-items: center;
    gap: 10px;
  }
  .brand-name {
    font-family: "Open Sans", Arial, sans-serif;
    font-weight: 300;
    font-size: 21px;
    line-height: 1.05;
    color: var(--brand-name);
    text-align: right;
  }
  .brand-dot {
    width: 26px; height: 26px;
    border-radius: 50%;
    background: var(--violet);
    flex: none;
  }
  .letterhead .brand-name { font-size: 21px; }

  .contact {
    margin-top: 34px;
    margin-left: auto;
    width: 170px;
    font-size: 9.5px;
    font-weight: 600;
    line-height: 1.55;
    color: var(--ink);
  }
  .contact-line { display: flex; align-items: center; gap: 5px; }
  .contact-icon {
    width: 11px; height: 11px;
    border-radius: 50%;
    display: inline-flex; align-items: center; justify-content: center;
    flex: none;
  }
  .contact-icon.phone { background: var(--blue); }
  .contact-icon.mail { background: var(--purple); }
  .contact-icon.web { background: var(--teal); }
  .contact-icon svg { width: 7px; height: 7px; }

  .letter-body {
    margin-top: 14px;
    font-size: 9.4px;
    line-height: 1.5;
    color: var(--ink);
  }
  .salutation { margin-bottom: 8px; color: var(--ink-soft); }
  .letter-body p.paragraph { text-indent: 12px; margin-bottom: 8px; }
  .closing { margin-top: 6px; color: var(--ink-soft); }
  .signature {
    margin-top: 12px;
    width: 80px; height: 38px;
    background: linear-gradient(90deg, #e4e4e8, #f2f2f4);
    border-radius: 3px;
  }

  .letter-mist {
    position: absolute;
    right: 40px; bottom: -60px;
    width: 240px; height: 240px;
    border-radius: 50%;
    background: radial-gradient(circle at 40% 40%, var(--mist-blue), var(--mist-purple));
    opacity: 0.85;
  }

  /* Envelope */
  .envelope {
    position: absolute;
    left: 600px; top: 260px;
    width: 560px; height: 282px;
    background: var(--paper);
    box-shadow: 0 6px 22px rgba(0,0,0,0.10);
  }
  .envelope-flap {
    position: absolute;
    inset: 0;
  }
  .envelope .brand {
    position: absolute;
    right: 52px; top: 96px;
  }
  .envelope .brand-name { font-size: 19px; }
  .envelope .brand-dot { width: 24px; height: 24px; }
</style>
</head>
<body>

<section class="letterhead" aria-label="Letterhead">
  <header class="brand">
    <div class="brand-name">Bright Harbor<br>Counseling</div>
    <span class="brand-dot"></span>
  </header>

  <address class="contact" style="font-style: normal;">
    <div>4120 Marlow Avenue</div>
    <div>Westfield, CA, 90455</div>
    <div class="contact-line">
      <span class="contact-icon phone">
        <svg viewBox="0 0 10 10"><path d="M2.2 1.2l1.6 0 .6 2-1 .8a5 5 0 0 0 2.6 2.6l.8-1 2 .6v1.6c0 .6-.5 1-1 1A7.8 7.8 0 0 1 1.2 2.2c0-.5.4-1 1-1z" fill="#fff"/></svg>
      </span>0412 555 018
    </div>
    <div class="contact-line">
      <span class="contact-icon mail">
        <svg viewBox="0 0 10 10"><rect x="1" y="2.5" width="8" height="5.5" fill="none" stroke="#fff" stroke-width="1"/><path d="M1 2.5l4 3 4-3" fill="none" stroke="#fff" stroke-width="1"/></svg>
      </span>hello@brightharbor.com
    </div>
    <div class="contact-line">
      <span class="contact-icon web">
        <svg viewBox="0 0 10 10"><circle cx="5" cy="5" r="3.8" fill="none" stroke="#fff" stroke-width="0.9"/><path d="M1.2 5h7.6M5 1.2c-2 2.4-2 5.2 0 7.6M5 1.2c2 2.4 2 5.2 0 7.6" fill="none" stroke="#fff" stroke-width="0.8"/></svg>
      </span>www.brightharbor.com
    </div>
  </address>

  <div class="letter-body">
    <p class="salutation">Dear customer,</p>
    <p class="paragraph">Lorem ipsum dolor sit amet, consectetur adipisicing elit, sed do eiusmod tempor incididunt ut labore et dolore magna aliqua. Ut enim ad minim veniam, quis nostrud exercitation ullamco laboris nisi ut aliquip ex ea commodo consequat. Duis aute irure dolor in reprehenderit in voluptate velit esse cillum dolore eu fugiat nulla pariatur. Excepteur sint occaecat cupidatat non proident, sunt in culpa qui officia deserunt mollit anim id est laborum.</p>
    <p class="paragraph">Lorem ipsum dolor sit amet, consectetur adipisicing elit, sed do eiusmod tempor incididunt ut labore et dolore magna aliqua. Ut enim ad minim veniam, quis nostrud exercitation ullamco laboris nisi ut aliquip ex ea commodo consequat. Duis aute irure dolor in reprehenderit in voluptate velit esse cillum dolore eu fugiat nulla pariatur. Excepteur sint occaecat cupidatat non proident, sunt in culpa qui officia deserunt mollit anim id est laborum.</p>
    <p class="paragraph">Lorem ipsum dolor sit amet, consectetur adipisicing elit, sed do eiusmod tempor incididunt ut labore et dolore magna aliqua. Ut enim ad minim veniam, quis nostrud exercitation ullamco laboris nisi ut aliquip ex ea commodo consequat. Duis aute irure dolor in reprehenderit in voluptate velit esse cillum dolore eu fugiat nulla pariatur. Excepteur sint occaecat cupidatat non proident, sunt in culpa qui officia deserunt mollit anim id est laborum.</p>
    <p class="paragraph">Lorem ipsum dolor sit amet, consectetur adipisicing elit, sed do eiusmod tempor incididunt ut labore et dolore magna aliqua. Ut enim ad minim veniam, quis nostrud exercitation ullamco laboris nisi ut aliquip ex ea commodo consequat. Duis aute irure dolor.</p>
    <p class="closing">Yours Sincerely,</p>
    <div class="signature" role="img" aria-label="Handwritten signature"></div>
  </div>

  <div class="letter-mist" aria-hidden="true"></div>
</section>

<section class="envelope" aria-label="Envelope">
  <svg class="envelope-flap" viewBox="0 0 560 282" preserveAspectRatio="none" aria-hidden="true">
    <path d="M14 0 L26 52 Q28 60 36 60 L524 60 Q532 60 534 52 L546 0" fill="none" stroke="var(--flap-line)" stroke-width="1.5"/>
  </svg>
  <div class="brand">
    <div class="brand-name">Bright Harbor<br>Counseling</div>
    <span class="brand-dot"></span>
  </div>
</section>

</body>
</html>
```